Accountability Project Graphics

I want to create 10 social media graphics (new Instagram size 4:5 (1080 x 1350 pixels) focusing on our Quilvo Accountability App, using any of the 3 pictures attached. Use the attached pics only, NO RANDOM STOCK PHOTOGRAPHY. For the color scheme, use the landing page colors/fonts (attached).
You can add any of the 3 photos attached but I mainly need BOLD text that includes these headlines and sub-headlines on them.
Please NOTE for all the headlines below, also add this sub-headline on each graphic:
Stay Consistent with RT in Your Pocket!
Here are the headlines:
• Stop Starting Over Every Monday
• You don't need more willpower. You need more support
• Built for women who are tired of doing this alone
• When Motivation Fades, RT Checks In
• The Support System You've Been Missing
• Support When Motivation Disappears
• What if RT Checked in Every Day?
• The Missing Piece Isn't Another Diet
• Eat the food you love. Stay accountable every day.
• One Bad Meal Doesn't Mean You Failed
women over 40 trying to lose weight

```html
<!DOCTYPE html>
<html lang="en">
<head>
<meta charset="utf-8">
<title>Accountability App Social Graphics</title>
<link href="https://fonts.googleapis.com/css2?family=Roboto:ital,wght@0,400;0,500;0,700;0,900;1,700&display=swap" rel="stylesheet">
<style>
  :root {
    --canvas: #eeeeee;
    --plum: #2e1a3f;
    --rose: #d94f7d;
    --white: #ffffff;
    --blush: #f3d5df;
    --blush-deep: #e6c6d6;
    --gold: #e9d9a2;
    --photo-skin: #b07a62;
    --photo-dark: #25263a;
  }
  * { margin: 0; padding: 0; box-sizing: border-box; }
  html, body { width: 1200px; height: 980px; overflow: hidden; background: var(--canvas); }
  body { position: relative; font-family: "Roboto", Arial, sans-serif; color: var(--plum); }

  .post { position: absolute; width: 356px; height: 445px; overflow: hidden; }
  .post--light { background: linear-gradient(180deg, #fff 0%, #fdf6f8 100%); }
  .post--blush { background: linear-gradient(180deg, var(--blush) 0%, var(--blush-deep) 100%); }

  .post-stop { left: 20px; top: 21px; }
  .post-willpower { left: 406px; top: 21px; }
  .post-support { left: 806px; top: 272px; }
  .post-women { left: 20px; top: 495px; }
  .post-motivation { left: 406px; top: 495px; }

  .photo { position: absolute; }
  .floral { position: absolute; border-radius: 50%; opacity: .5; }

  .headline { position: absolute; font-weight: 700; line-height: 1; white-space: nowrap; }
  .accent { color: var(--rose); }

  .pill {
    position: absolute; height: 32px; width: 260px; left: 48px;
    background: var(--plum); border: 2px solid var(--rose); border-radius: 16px;
    color: var(--white); font-style: italic; font-weight: 700; font-size: 12.5px;
    display: flex; align-items: center; justify-content: center; white-space: nowrap;
  }

  .brush { position: absolute; }
  .brush-text { position: absolute; color: var(--white); white-space: nowrap; }

  .frame { position: absolute; border: 1.5px solid var(--gold); }

  .post-stop .headline { left: 0; width: 356px; text-align: center; font-size: 37px; font-weight: 500; }

  .stack { position: absolute; left: 23px; font-weight: 700; text-transform: uppercase; }
  .stack span { display: block; }
</style>
</head>
<body>

<section class="post post--light post-stop">
  <div class="floral" style="left:-30px;top:240px;width:90px;height:120px;background:#f4a9a4;"></div>
  <div class="floral" style="left:250px;top:-20px;width:110px;height:60px;background:#b9d3ae;"></div>
  <div class="photo" role="img" aria-label="Photo of two women hugging and laughing"
       style="left:60px;top:165px;width:290px;height:280px;background:radial-gradient(ellipse at 55% 40%, var(--photo-skin) 0%, #c25683 40%, #e8d7e4 70%, rgba(255,255,255,0) 100%);"></div>
  <h1 class="headline" style="top:22px;">Stop Starting Over</h1>
  <h1 class="headline accent" style="top:69px;">Every Monday</h1>
  <p class="pill" style="top:124px;">Stay Consistent with RT in Your Pocket!</p>
</section>

<section class="post post--light post-willpower">
  <div class="floral" style="left:220px;top:-20px;width:110px;height:60px;background:#f4b7b7;"></div>
  <div class="floral" style="left:-20px;top:390px;width:110px;height:70px;background:#f6c4c4;"></div>
  <div class="frame" style="left:23px;top:21px;width:312px;height:410px;"></div>
  <div class="photo" role="img" aria-label="Photo of a smiling woman in a black lace top and jeans, hand on hip"
       style="left:238px;top:12px;width:119px;height:433px;background:linear-gradient(180deg, #3a2b2b 0%, var(--photo-dark) 22%, #1f2538 100%);border-radius:60px 60px 0 0;"></div>
  <h2 class="stack" style="top:36px;font-size:41px;line-height:47.5px;">
    <span>You</span><span>Don't</span><span>Need</span><span>More <em class="accent" style="font-style:normal;">Will</em></span><span>Power</span>
  </h2>
  <svg class="brush" style="left:0;top:262px;" width="236" height="114" viewBox="0 0 236 114">
    <path d="M0 28 L40 20 L120 12 L200 4 L228 0 L222 18 L232 30 L224 60 L236 70 L220 82 L150 94 L60 108 L0 114 Z" fill="var(--rose)"/>
  </svg>
  <p class="brush-text" style="left:22px;top:292px;font-size:22px;font-weight:500;line-height:31px;">YOU NEED MORE<br>SUPPORT</p>
  <p class="pill" style="top:398px;">Stay Consistent with RT in Your Pocket!</p>
</section>

<section class="post post--light post-support">
  <div class="floral" style="left:260px;top:-20px;width:100px;height:60px;background:#f4b7b7;"></div>
  <div class="frame" style="left:23px;top:23px;width:312px;height:408px;"></div>
  <div class="photo" role="img" aria-label="Photo of a smiling woman in a black lace top and jeans, hand on hip"
       style="left:222px;top:12px;width:135px;height:433px;background:linear-gradient(180deg, #3a2b2b 0%, var(--photo-dark) 22%, #1f2538 100%);border-radius:60px 60px 0 0;"></div>
  <h2 class="stack" style="top:38px;font-size:42px;line-height:54px;">
    <span>The</span><span>Support</span><span>System</span><span class="accent">You've</span><span class="accent">Been</span><span class="accent">Missing</span>
  </h2>
  <svg class="brush" style="left:0;top:335px;" width="260" height="110" viewBox="0 0 260 110">
    <path d="M0 78 L120 40 L230 6 L252 0 L248 20 L260 28 L244 50 L170 76 L60 104 L0 110 Z" fill="var(--rose)"/>
  </svg>
  <p class="brush-text" style="left:9px;top:420px;font-size:12.5px;line-height:15px;font-weight:700;font-style:italic;transform:rotate(-16.5deg);transform-origin:left center;">Stay Consistent with RT in Your Pocket!</p>
</section>

<section class="post post--blush post-women">
  <h2 class="headline" style="left:0;width:356px;text-align:center;top:17px;font-size:31px;font-weight:700;">BUILT FOR WOMEN</h2>
  <svg class="brush" style="left:28px;top:56px;" width="300" height="112" viewBox="0 0 300 112">
    <path d="M10 40 L160 14 L280 0 L296 10 L288 36 L300 50 L286 70 L170 92 L40 112 L30 96 L0 90 L14 66 Z" fill="var(--rose)"/>
  </svg>
  <p class="brush-text" style="left:0;width:356px;text-align:center;top:80px;font-size:23px;line-height:31px;">Who Are Tired<br>Of Doing This Alone</p>
  <div class="photo" role="img" aria-label="Photo of two women in denim laughing together"
       style="left:52px;top:144px;width:262px;height:301px;background:linear-gradient(180deg, #4a3328 0%, #3a4a6a 35%, #34466a 100%);border-radius:70px 70px 0 0;"></div>
  <p class="pill" style="top:399px;">Stay Consistent with RT in Your Pocket!</p>
</section>

<section class="post post--blush post-motivation">
  <h2 class="headline" style="left:0;width:356px;text-align:center;top:16px;font-size:46px;font-weight:900;line-height:59px;white-space:normal;">WHEN<br>MOTIVATION<br>FADES</h2>
  <div class="photo" role="img" aria-label="Photo of two women hugging and laughing"
       style="left:0;top:185px;width:205px;height:260px;background:radial-gradient(ellipse at 50% 40%, var(--photo-skin) 0%, #c25683 40%, #e3cfe0 72%, rgba(255,255,255,0) 100%);"></div>
  <p class="headline accent" style="left:190px;width:162px;text-align:center;top:226px;font-size:28px;line-height:38px;">RT CHECKS<br>IN</p>
  <svg class="brush" style="left:45px;top:368px;" width="290" height="77" viewBox="0 0 290 77">
    <path d="M0 40 L120 22 L250 0 L270 6 L290 20 L276 44 L284 77 L10 77 L20 60 Z" fill="var(--rose)"/>
  </svg>
  <p class="brush-text" style="left:0;width:356px;text-align:center;top:418px;font-size:12.5px;font-weight:700;font-style:italic;">Stay Consistent with RT in Your Pocket!</p>
</section>

</body>
</html>
```